Etiketten-Design für Rotwein
Zielgruppe
Weinkellerei aus Baden (Deutschland) mit Fokus im Lebensmittelhandel in Deutschland
Aufgabenstellung
Wir suchen ein Frontetikett für einen modernen badischen Rotwein (Cuvée Lumen) mit dem Namen 'Die stille Seite vom Hang'
Aus dem Etikett soll hervorgehen, dass es sich nicht um einen klassischen, leichten deutschen Rotwein handelt, sondern um einen kräftigen, gehaltvollen, mediterran anmutenden Rotwein mit purpurroter Farbe und vollmundigem, nachhaltigem Geschmack. (Geschmacksrichtung feinherb)
Zielgruppe Discount-Kunden, Männlich/Weiblich, Alter: 25-60 Jahre, wird für unter € 5,-/Fl. verkauft.
Weinbeschreibung:
Farbe: Ein wunderschönes tiefdunkles purpurrot mit violetten Reflexen
Duft: In der Nase zeigen sich Aromen nach Waldbeeren, sowie Anklänge von Rauch, Röstaromen, Nelke, etwas Vanille und dunkle Schokolade
Geschmack: Geschmacklich füllig und kraftvoll, Brombeeraromen und schön eingebundenen Tanninen. Langanhaltend intensiv im Abgang.
Anforderungen Etikett:
Maße: Höhe max. 120mm/Breite max. 80mm (darf auch kleiner oder quadratisch sein)
SK Etikett, Naturstruktur bis 90g (m²) (Ein - oder zweiteilig)
Eine figürliche Etikettenkontur ist möglich, es wird aber am rechten Etikettenrand eine gerade Spendekante benötigt um das Etikett maschinell verarbeiten zu können.
Als Flasche wird eine 0,75 L Bordeauxflasche (Farbe: grün) eingesetzt.
Verschluss: Longcap
Mögliche Veredelungen: Quelllack, Prägungen, Heissfolie, Glanzlack
Pflichtangaben:
Die stille Seite vom Hang

```html
<!DOCTYPE html>
<html lang="de">
<head>
<meta charset="utf-8">
<title>Die stille Seite vom Hang – Cuvée Lumen Etikett</title>
<link rel="stylesheet" href="https://fonts.googleapis.com/css2?family=Baloo+2:wght@700&family=Lato:wght@400&display=swap">
<style>
  :root {
    --indigo-deep: #22077a;
    --violet: #5a1283;
    --magenta: #a3186f;
    --crimson: #e3152a;
    --coral: #d9584e;
    --wine: #6e1c45;
    --wine-dark: #3c1546;
    --accent-line: #e0a21b;
    --ink-light: #ffffff;
  }
  html, body {
    margin: 0;
    padding: 0;
    width: 727px;
    height: 1200px;
    overflow: hidden;
    background: var(--indigo-deep);
  }
  .label {
    position: relative;
    width: 727px;
    height: 1200px;
    overflow: hidden;
    font-family: "Lato", sans-serif;
    color: var(--ink-light);
  }
  .label__backdrop {
    position: absolute;
    inset: 0;
    width: 100%;
    height: 100%;
  }
  .label__cuvee {
    position: absolute;
    left: 53px;
    top: 52px;
    margin: 0;
    font-size: 34px;
    font-weight: 400;
    letter-spacing: 0.2px;
  }
  .label__title {
    position: absolute;
    inset: 0;
    margin: 0;
    font-family: "Baloo 2", sans-serif;
    font-weight: 700;
    font-size: 88px;
    line-height: 1;
  }
  .title-word {
    position: absolute;
    display: block;
    white-space: nowrap;
  }
  .title-word--die    { left: 222px; top: 316px; transform: rotate(2deg); }
  .title-word--stille { left: 300px; top: 452px; transform: rotate(-8deg); text-transform: uppercase; }
  .title-word--seite  { left: 178px; top: 580px; transform: rotate(-3deg); }
  .title-word--vom    { left: 420px; top: 636px; transform: rotate(-6deg); }
  .title-word--hang   { left: 196px; top: 754px; transform: rotate(3deg); }
  .label__vintage {
    position: absolute;
    right: 42px;
    bottom: 56px;
    margin: 0;
    font-size: 37px;
    line-height: 1.2;
    text-align: left;
  }
  .label__vintage span { display: block; }
</style>
</head>
<body>
<main class="label">
  <svg class="label__backdrop" viewBox="0 0 727 1200" aria-hidden="false">
    <defs>
      <linearGradient id="bg-vertical" x1="0" y1="0" x2="0" y2="1">
        <stop offset="0" stop-color="var(--indigo-deep)"/>
        <stop offset="0.2" stop-color="var(--violet)"/>
        <stop offset="0.5" stop-color="var(--magenta)"/>
        <stop offset="0.72" stop-color="var(--crimson)"/>
        <stop offset="0.88" stop-color="var(--violet)"/>
        <stop offset="1" stop-color="var(--indigo-deep)"/>
      </linearGradient>
      <radialGradient id="bg-glow" cx="0.45" cy="0.66" r="0.55">
        <stop offset="0" stop-color="var(--crimson)" stop-opacity="0.9"/>
        <stop offset="0.6" stop-color="var(--crimson)" stop-opacity="0.3"/>
        <stop offset="1" stop-color="var(--crimson)" stop-opacity="0"/>
      </radialGradient>
      <linearGradient id="bg-sides" x1="0" y1="0" x2="1" y2="0">
        <stop offset="0" stop-color="var(--coral)" stop-opacity="0.35"/>
        <stop offset="0.3" stop-color="var(--coral)" stop-opacity="0"/>
        <stop offset="0.8" stop-color="var(--indigo-deep)" stop-opacity="0"/>
        <stop offset="1" stop-color="var(--indigo-deep)" stop-opacity="0.7"/>
      </linearGradient>
      <radialGradient id="marble-fill" cx="0.45" cy="0.45" r="0.6">
        <stop offset="0" stop-color="var(--wine-dark)"/>
        <stop offset="0.55" stop-color="var(--wine)"/>
        <stop offset="0.9" stop-color="#9a1a3a"/>
        <stop offset="1" stop-color="var(--crimson)"/>
      </radialGradient>
    </defs>
    <rect class="backdrop__base" width="727" height="1200" fill="url(#bg-vertical)"/>
    <rect class="backdrop__glow" width="727" height="1200" fill="url(#bg-glow)"/>
    <rect class="backdrop__sides" width="727" height="1200" fill="url(#bg-sides)"/>
    <line class="accent-line accent-line--upper" x1="86" y1="194" x2="196" y2="366" stroke="var(--accent-line)" stroke-width="2"/>
    <circle class="marble-disc" cx="369" cy="578" r="308" fill="url(#marble-fill)" role="img" aria-label="Abstrakte Marmorierung in Weinrot, Violett und Leuchtrot als Kreisfläche"/>
    <line class="accent-line accent-line--lower" x1="432" y1="734" x2="612" y2="1008" stroke="var(--accent-line)" stroke-width="2"/>
  </svg>

  <p class="label__cuvee">Cuvée Lumen</p>

  <h1 class="label__title">
    <span class="title-word title-word--die">Die</span>
    <span class="title-word title-word--stille">stille</span>
    <span class="title-word title-word--seite">Seite</span>
    <span class="title-word title-word--vom">vom</span>
    <span class="title-word title-word--hang">Hang</span>
  </h1>

  <p class="label__vintage"><span>20</span><span>21</span></p>
</main>
</body>
</html>
```